Venture Capital firm needs modern business cards

We are a Venture Capital firm within financial services/Asset management. The industry generally has basic business cards with black, blue and maybe green/yellow design elements.
Our firm has a four-colour swoosh logo. We are based in London and want to stand out, just a little bit!, from the crowd. Our company is called LORV Investments and the 'C' stands for collaboration thus using makerswarm is a natural portal for our business card design competition. Our logo came via makerswarm too!
We use 'Venture Partner in Asset Management' as our tagline and this is Trademark registered. We operate in a conservative industry and we should not overstep our mark. The logo is colorful as it is and therefore the rest of the design should not be too fanciful.
The objective is twofold: make our logo element stick and memorable with our audience, whilst representing a conservative yet young image.
Updates
The Business Card obviously needs a field for Name, Surname, Job Title, Adress fields: Street, City, Postcode, Country, telefone and cell number, website address, etc.
We have uploaded the ai file. We trust that these are OK. If not, please advise.
Reason: We have have been busy with a client engagement. We will set the project as Guaranteed in return for the troubles we cause. Apologies for the confusion.
Thank you all for these great and creative design suggestions. The team is very happy with a number of your ideas! We will be in touch tomorrow to give individual feedback before the project closes on Friday. We look forward to working with some of you to narrow down your creations. Thank you, LORV Investments team.
All,
Target Market(s)
Financial Services Professionals, Investors, Media, 35-70 years, mainly male, well educated
Industry/Entity Type
Conservative
Requirements
Must have
- We must make use of our logo and potential tagline 'Venture Partner in Asset Management' as we are establishing a new Brand and new company in the market.
We can use 'LORV', 'LORV Investments', and 'LORV Investments'+tagline 'Venture Partner in Asset Management' or simply the four-colour swoosh plus the name of the company as part of the text. (see files)
All design elements are available in black or grey-scale if required. (grey scale swoosh attached).
Due to regulation we must have the following wording on the card in small print 'LORV Investments is an Appointed Representative of Bramwell Holdings Partnership Limited, which is authorised by the Monetary Oversight Board'.
Nice to have
- We would consider designs that make use of different printing techniques such embossing/debossing, UV spot etc.
We attach our colour palette in the files section for your reference.
Should not have
- The font we use for our company name is 'EXO' so do not use a font style that clashes with the corporate fonts, please.
Do not use other design elements than the ones we provide in the file library as part of this project.

```html
<!DOCTYPE html>
<html lang="en">
<head>
<meta charset="utf-8">
<title>LORV Investments – Business Card</title>
<link href="https://fonts.googleapis.com/css2?family=Exo:wght@300;400;500&family=Barlow:wght@400;500&display=swap" rel="stylesheet">
<style>
  :root {
    --backdrop: #a3a3a3;
    --card: #ffffff;
    --ink-dark: #3d3f40;
    --ink-grey: #8b8b8b;
    --ink-mid: #6f6f6f;
    --accent-green: #8cc63f;
    --accent-green-dark: #6fae2a;
  }
  * { box-sizing: border-box; margin: 0; padding: 0; }
  html, body {
    width: 1200px;
    height: 487px;
    overflow: hidden;
    background: var(--backdrop);
  }
  .sheet {
    position: relative;
    width: 1200px;
    height: 487px;
  }
  .card {
    position: absolute;
    top: 80px;
    width: 531px;
    height: 324px;
    background: var(--card);
    border-radius: 16px;
    overflow: hidden;
  }
  .card--front { left: 53px; }
  .card--back  { left: 607px; }

  /* Front: brand */
  .brand {
    position: absolute;
    left: 108px;
    top: 52px;
    display: flex;
    align-items: center;
    gap: 16px;
  }
  .brand__dot {
    width: 70px;
    height: 70px;
    border-radius: 50%;
    background: var(--ink-dark);
    flex: none;
  }
  .brand__name {
    font-family: "Exo", sans-serif;
    font-weight: 400;
    color: var(--ink-dark);
    line-height: 1;
  }
  .brand__word {
    display: block;
    font-size: 78px;
    letter-spacing: 1px;
  }
  .brand__sub {
    display: block;
    font-size: 17px;
    letter-spacing: 6px;
    margin-top: 2px;
    padding-left: 4px;
  }

  /* Front: holder */
  .holder {
    position: absolute;
    left: 27px;
    top: 234px;
    width: 177px;
    font-family: "Barlow", sans-serif;
    text-align: right;
  }
  .holder__name {
    font-size: 17px;
    font-weight: 500;
    color: var(--ink-grey);
    text-align: left;
    letter-spacing: 0.2px;
  }
  .holder__role {
    font-size: 14px;
    color: var(--accent-green);
    margin-top: 2px;
  }

  /* Front: contacts */
  .contacts {
    position: absolute;
    left: 245px;
    top: 233px;
    list-style: none;
    font-family: "Barlow", sans-serif;
    font-size: 13.5px;
    color: var(--ink-grey);
    line-height: 15.5px;
  }
  .contacts__row {
    display: flex;
    align-items: flex-start;
    gap: 6px;
  }
  .contacts__icon {
    width: 12px;
    height: 12px;
    flex: none;
    margin-top: 2px;
    fill: var(--accent-green);
  }
  .contacts__pair { display: flex; gap: 10px; }
  .contacts__pair span { display: flex; gap: 6px; }

  /* Back: tagline */
  .tagline {
    position: absolute;
    left: 155px;
    top: 80px;
    font-family: "Exo", sans-serif;
    font-weight: 300;
    color: var(--ink-grey);
    line-height: 1;
  }
  .tagline__small { display: block; font-size: 30px; }
  .tagline__big   { display: block; font-size: 47px; letter-spacing: -0.5px; }
  .tagline__line  { display: flex; align-items: flex-start; }
  .tagline__in    { font-size: 15px; margin-top: 12px; margin-right: 2px; padding-left: 22px; }
  .tagline__venture { margin-bottom: -2px; }
  .tagline__mgmt  { margin-top: 2px; }
  .tagline__url {
    display: block;
    font-family: "Barlow", sans-serif;
    font-weight: 400;
    font-size: 14.5px;
    margin-top: 8px;
    padding-left: 40px;
    color: var(--ink-grey);
  }
  .tagline__url strong { color: var(--accent-green-dark); font-weight: 500; }
</style>
</head>
<body>
<main class="sheet">

  <section class="card card--front" aria-label="Business card front">
    <div class="brand">
      <span class="brand__dot" aria-hidden="true"></span>
      <h1 class="brand__name">
        <span class="brand__word">LORV</span>
        <span class="brand__sub">Investments</span>
      </h1>
    </div>

    <div class="holder">
      <p class="holder__name">CARDHOLDER NAME</p>
      <p class="holder__role">Designation</p>
    </div>

    <ul class="contacts">
      <li class="contacts__row">
        <svg class="contacts__icon" viewBox="0 0 12 12" aria-hidden="true"><path d="M6 0a4 4 0 0 0-4 4c0 3 4 8 4 8s4-5 4-8a4 4 0 0 0-4-4zm0 5.6A1.6 1.6 0 1 1 6 2.4a1.6 1.6 0 0 1 0 3.2z"/></svg>
        <span>01 01 Avenue, Suite No. 123,<br>Your City, Country</span>
      </li>
      <li class="contacts__row contacts__pair">
        <span>
          <svg class="contacts__icon" viewBox="0 0 12 12" aria-hidden="true"><circle cx="6" cy="6" r="6"/><path d="M3.6 3.2l1.2-.4.8 1.6-.7.6a4.5 4.5 0 0 0 2.1 2.1l.6-.7 1.6.8-.4 1.2C6 8.8 3.2 6 3.6 3.2z" fill="#fff"/></svg>
          +012 345 6789
        </span>
        <span>
          <svg class="contacts__icon" viewBox="0 0 12 12" aria-hidden="true"><rect x="3" y="0.5" width="6" height="4"/><rect x="0.5" y="5" width="11" height="6.5" rx="1"/></svg>
          +012 345 6780
        </span>
      </li>
      <li class="contacts__row">
        <svg class="contacts__icon" viewBox="0 0 12 12" aria-hidden="true"><rect x="0" y="2" width="12" height="8" rx="1"/><path d="M1 3l5 3.5L11 3" stroke="#fff" stroke-width="1" fill="none"/></svg>
        <span>cardholder.name@lorvinvestments.com</span>
      </li>
      <li class="contacts__row">
        <svg class="contacts__icon" viewBox="0 0 12 12" aria-hidden="true"><circle cx="6" cy="6" r="6"/><path d="M0.5 6h11M6 0.5c-3 3.5-3 7.5 0 11M6 0.5c3 3.5 3 7.5 0 11" stroke="#fff" stroke-width="0.9" fill="none"/></svg>
        <span>www.lorvinvestments.com</span>
      </li>
    </ul>
  </section>

  <section class="card card--back" aria-label="Business card back">
    <p class="tagline">
      <span class="tagline__small tagline__venture">Venture</span>
      <span class="tagline__big">Partner</span>
      <span class="tagline__line"><span class="tagline__in">in</span><span class="tagline__big">Asset</span></span>
      <span class="tagline__small tagline__mgmt">Management</span>
      <span class="tagline__url">www.<strong>lorvinvestments</strong>.com</span>
    </p>
  </section>

</main>
</body>
</html>
```